Brightway Carpet and Tile cleaning Business card Design

I need a design that has the same feel as my van.
i would also like a prominent "Review us on facebook" somewhere, but not that it makes it look silly.
I would like the card to have a little bit of grey or black in the design as well.

It will need contact details
phone: 0455 817264
email: rkbrightwayclean@mailbox-example.com
website: www.brightwaycarpetandtilecleaning-example.com.au
facebook: /brightwaycarpetandtilecleaning

Industry/Entity Type

Business

Contact Information for Business Card

Phone number 0455817264
Email rkbrightwayclean@mailbox-example.com
Website www.brightwaycarpetandtilecleaning-example.com.au
Facebook/brightwaycarpetandtilecleaning

Colors
000000

Requirements
Must have
• Same feel as my van
• I want the card to stand out from the crowd
Nice to have
• Maybe include a tiny bit of a third colour? Grey's,blacks, orange?

```html
<!DOCTYPE html>
<html lang="en">
<head>
<meta charset="utf-8">
<title>Brightway Carpet and Tile cleaning – Business Card</title>
<link rel="stylesheet" href="https://fonts.googleapis.com/css2?family=Open+Sans:wght@400;600;700;800&display=swap">
<style>
  :root {
    --stage: #3b3b3b;
    --aqua: #1bb4e2;
    --aqua-light: #8fdcf4;
    --aqua-pale: #e6f6fc;
    --ink: #5a5a5a;
    --rule: #c9c9c9;
    --white: #ffffff;
    --night: #050607;
    --button-top: #7f9bd6;
    --button-bottom: #3e5fae;
    --button-ink: #0d1530;
    --sans: "Open Sans", Arial, sans-serif;
  }
  * { box-sizing: border-box; margin: 0; padding: 0; }
  html, body { width: 1105px; height: 1200px; overflow: hidden; }
  body { background: var(--stage); font-family: var(--sans); position: relative; }

  .card { position: absolute; left: 196px; width: 720px; height: 412px; overflow: hidden; }
  .card--front { top: 145px; background: var(--white); }
  .card--back { top: 602px; background: var(--night); }

  .front__bubbles {
    position: absolute; inset: 0;
    background: radial-gradient(circle at 30% 75%, var(--aqua-pale) 0, rgba(230,246,252,0) 45%),
                radial-gradient(circle at 85% 60%, var(--aqua-pale) 0, rgba(230,246,252,0) 40%),
                var(--white);
  }
  .front__band { position: absolute; left: 0; top: 0; width: 720px; height: 150px; }

  .holder { position: absolute; right: 70px; top: 34px; text-align: right; color: var(--white); }
  .holder__name { font-size: 30px; font-weight: 600; line-height: 1.2; }
  .holder__role { font-size: 20px; font-weight: 400; margin-top: 2px; }

  .brand { position: absolute; display: flex; align-items: center; gap: 12px; }
  .brand__dot { width: 30px; height: 30px; border-radius: 50%; background: var(--aqua); flex: none; }
  .brand__name { font-weight: 800; line-height: 1.05; color: var(--aqua); }
  .card--front .brand { left: 30px; top: 232px; }
  .card--front .brand__name { font-size: 27px; }

  .divider { position: absolute; left: 322px; top: 207px; width: 1px; height: 158px; background: var(--rule); }

  .contacts { position: absolute; left: 340px; top: 214px; list-style: none; }
  .contacts li { display: flex; align-items: center; gap: 10px; height: 28px; font-size: 13.5px; color: var(--ink); white-space: nowrap; }
  .contacts svg { width: 17px; height: 17px; flex: none; }

  .back__glow {
    position: absolute; inset: 0;
    background: linear-gradient(105deg, rgba(0,0,0,0) 0 50%, rgba(70,74,72,0.55) 58%, rgba(20,22,21,0.2) 75%, rgba(0,0,0,0) 100%),
                radial-gradient(circle at 20% 40%, rgba(60,80,60,0.35) 0, rgba(0,0,0,0) 40%),
                radial-gradient(circle at 80% 60%, rgba(50,80,60,0.35) 0, rgba(0,0,0,0) 40%),
                var(--night);
  }
  .card--back .brand { left: 50%; top: 140px; transform: translateX(-50%); }
  .card--back .brand__name { font-size: 48px; white-space: nowrap; }
  .card--back .brand__dot { width: 40px; height: 40px; }

  .review {
    position: absolute; left: 200px; top: 323px; width: 320px; height: 44px;
    border-radius: 5px; border: 1px solid #c9d6f2;
    background: linear-gradient(var(--button-top), var(--button-bottom));
    color: var(--button-ink); font-weight: 800; font-size: 22px;
    display: flex; align-items: center; justify-content: center; letter-spacing: 0.2px;
  }
</style>
</head>
<body>

<section class="card card--front" aria-label="Business card front">
  <div class="front__bubbles" role="img" aria-label="Soft pale blue soap bubble pattern"></div>
  <svg class="front__band" viewBox="0 0 720 150" aria-hidden="true">
    <defs>
      <linearGradient id="bandFill" x1="0" y1="0" x2="1" y2="0">
        <stop offset="0" stop-color="#8fdcf4"/>
        <stop offset="1" stop-color="#1bb4e2"/>
      </linearGradient>
    </defs>
    <path d="M0 0 H720 V125 Q360 150 0 110 Z" fill="url(#bandFill)"/>
  </svg>

  <div class="holder">
    <p class="holder__name">Rick Kellerman</p>
    <p class="holder__role">owner/operator</p>
  </div>

  <div class="brand">
    <span class="brand__dot"></span>
    <p class="brand__name">Brightway<br>Carpet &amp; Tile<br>Cleaning</p>
  </div>

  <div class="divider"></div>

  <ul class="contacts">
    <li>
      <svg viewBox="0 0 24 24" aria-hidden="true"><path fill="#1bb4e2" d="M6.6 10.8a15 15 0 0 0 6.6 6.6l2.2-2.2a1 1 0 0 1 1-.25 11.4 11.4 0 0 0 3.6.57 1 1 0 0 1 1 1V20a1 1 0 0 1-1 1A17 17 0 0 1 3 4a1 1 0 0 1 1-1h3.5a1 1 0 0 1 1 1c0 1.25.2 2.45.57 3.57a1 1 0 0 1-.25 1Z"/></svg>
      0455817264
    </li>
    <li>
      <svg viewBox="0 0 24 24" aria-hidden="true"><rect x="2" y="5" width="20" height="14" rx="1.5" fill="#1bb4e2"/><path d="M3 6.5l9 6.5 9-6.5" fill="none" stroke="#fff" stroke-width="1.6"/></svg>
      rkbrightwayclean@mailbox-example.com
    </li>
    <li>
      <svg viewBox="0 0 24 24" aria-hidden="true"><circle cx="12" cy="12" r="10" fill="#1bb4e2"/><path d="M2 12h20M12 2c3 3 3 17 0 20M12 2c-3 3-3 17 0 20" fill="none" stroke="#fff" stroke-width="1.4"/></svg>
      brightwaycarpetandtilecleaning-example.com.au
    </li>
    <li>
      <svg viewBox="0 0 24 24" aria-hidden="true"><rect x="3" y="3" width="18" height="18" rx="2" fill="#1bb4e2"/></svg>
      /brightwaycarpetandtilecleaning
    </li>
  </ul>
</section>

<section class="card card--back" aria-label="Business card back">
  <div class="back__glow" role="img" aria-label="Dark bokeh bubble pattern with sparkles and a glossy sheen"></div>

  <div class="brand">
    <span class="brand__dot"></span>
    <p class="brand__name">Brightway Clean</p>
  </div>

  <div class="review">REVIEW US ONLINE</div>
</section>

</body>
</html>
```